New Business card design to reflect rebrand

I would like a business card design with a good base colour for our new logo and also a placeholder for a profile pic of the card holder. the design needs to be editable to the point that we can easily change the picture of the person and use that design for printmerlo etc. we are looking at a metalic finish business card so will need a good base colour to bring out the finish.

Target Market(s)

prospective customers

Industry/Entity Type

Business

Contact Information for Business Card

I would like one editable design that we can change the name of the card holder and profile picture. The design need to be in a format that be send to printmerlo etc.

Our address is Fenwick Lodge, Copse Lane, Ashby Marsh, GU14 3TP Tel no. 01483 556172

Requirements
Must have
• place holder for a profile pic for the card holder. in AI or preferably PSD format

```html
<!DOCTYPE html>
<html lang="en">
<head>
<meta charset="utf-8">
<title>Brightmoor Workplace Services – Business Card</title>
<link rel="stylesheet" href="https://fonts.googleapis.com/css2?family=Open+Sans:wght@400;600;700&display=swap">
<style>
  :root {
    --page-bg: #2c2724;
    --card-bg: #0e0e10;
    --brand-orange: #f26a1b;
    --brand-slate: #5d7089;
    --text-light: #f2f2f2;
    --photo-top: #2a2d3a;
    --photo-bottom: #141826;
  }
  * { box-sizing: border-box; margin: 0; padding: 0; }
  html, body {
    width: 1200px; height: 844px; overflow: hidden;
    background: var(--page-bg);
    font-family: "Open Sans", Arial, sans-serif;
  }
  .sheet {
    position: relative; width: 1200px; height: 844px;
    display: flex; align-items: center; justify-content: center; gap: 40px;
  }
  .card {
    position: relative; width: 550px; height: 314px;
    background: var(--card-bg); overflow: hidden;
    box-shadow: 0 14px 30px rgba(0,0,0,.45);
  }
  /* Front */
  .card-front .brand-name {
    position: absolute; left: 40px; top: 66px;
    font-size: 32px; font-weight: 700; letter-spacing: 1px;
    color: var(--brand-orange);
  }
  .holder-photo {
    position: absolute; right: 0; top: 0; width: 250px; height: 100%;
    background: linear-gradient(180deg, var(--photo-top), var(--photo-bottom));
  }
  .contact {
    position: absolute; left: 40px; top: 178px; color: var(--text-light);
    font-size: 13.5px; line-height: 1.55;
  }
  .contact .holder-name {
    font-size: 18px; font-weight: 700; color: var(--brand-orange); margin-bottom: 4px;
  }
  .contact .row { display: flex; align-items: center; gap: 8px; }
  .contact .row svg { width: 11px; height: 11px; fill: var(--brand-orange); flex: none; }
  .contact .address { margin-top: 6px; }
  /* Back */
  .card-back { display: flex; align-items: center; justify-content: center; }
  .card-back .brand-name {
    font-size: 38px; font-weight: 700; letter-spacing: 2px;
    color: var(--brand-slate);
  }
</style>
</head>
<body>
<main class="sheet">
  <section class="card card-front">
    <div class="brand-name">BRIGHTMOOR</div>
    <div class="holder-photo" role="img" aria-label="Profile photo of the card holder"></div>
    <div class="contact">
      <div class="holder-name">Daniel Reeve</div>
      <div class="row">
        <svg viewBox="0 0 24 24" aria-hidden="true"><path d="M6.6 10.8a15.1 15.1 0 0 0 6.6 6.6l2.2-2.2a1 1 0 0 1 1-.25 11.4 11.4 0 0 0 3.6.57 1 1 0 0 1 1 1V20a1 1 0 0 1-1 1A17 17 0 0 1 3 4a1 1 0 0 1 1-1h3.5a1 1 0 0 1 1 1c0 1.25.2 2.45.57 3.57a1 1 0 0 1-.25 1z"/></svg>
        <span>01483 556172</span>
      </div>
      <div class="row">
        <svg viewBox="0 0 24 24" aria-hidden="true"><path d="M2 5h20v14H2z"/><path d="M3 6.5l9 7 9-7" fill="none" stroke="#0e0e10" stroke-width="2"/></svg>
        <span>info@brightmoor.com</span>
      </div>
      <div class="address">Fenwick Lodge, Copse Lane,<br>Ashby Marsh, GU14 3TP</div>
    </div>
  </section>

  <section class="card card-back">
    <div class="brand-name">BRIGHTMOOR</div>
  </section>
</main>
</body>
</html>
```